Graphics for Book geared to Professionals

We need the attached graphics professional recreated for our book. The book will be in black and white so it will need to be grey scale. Please see the best practices for graphics from our publisher Harrowgate.
The power point attached has several graphics that we need professional illustrated. The graphics in a excel format simply need to be transposed professionally (slides 8-14). The graphs in the other slides need to have some design put behind them. These make the general look and feel somewhat consistent. If you have any questions, you can email me at martin.coyle@brindlework.com.

Target Market(s)

Professionals, Business Analyst

Industry/Entity Type

It Professional

Font styles to use
Other font styles liked:
• Calibre

Requirements
Must have
• Professional looks and feel

```html
<!DOCTYPE html>
<html lang="en">
<head>
<meta charset="utf-8">
<title>Analytical Cycle</title>
<link rel="stylesheet" href="https://fonts.googleapis.com/css2?family=Carlito:wght@400;700&display=swap">
<style>
  :root {
    --page: #ffffff;
    --frame: #5a5a5a;
    --ink: #111111;
    --disc-light: #ffffff;
    --disc-mid: #e4e4e4;
    --disc-dark: #b9b9b9;
    --side-light: #c8c8c8;
    --side-dark: #6f6f6f;
    --arrow-dark: #3a3a3a;
    --arrow-mid: #8a8a8a;
    --arrow-light: #e8e8e8;
  }
  html, body {
    margin: 0;
    padding: 0;
    width: 1072px;
    height: 1200px;
    overflow: hidden;
    background: var(--page);
  }
  .canvas {
    display: block;
    width: 1072px;
    height: 1200px;
    font-family: "Carlito", "Calibri", Arial, sans-serif;
  }
  .frame { fill: none; stroke: var(--frame); stroke-width: 3; }
  .title {
    font-size: 62px;
    font-weight: 700;
    fill: var(--ink);
    text-anchor: middle;
  }
  .node-label {
    font-size: 52px;
    font-weight: 700;
    fill: var(--ink);
    text-anchor: middle;
  }
  .node-side { fill: url(#sideShade); }
  .node-top { fill: url(#topShade); stroke: #d0d0d0; stroke-width: 1.5; }
  .node-shadow { fill: #000; opacity: 0.18; filter: url(#soften); }
  .arrow-h { fill: url(#arrowHorizontal); }
  .arrow-h-rev { fill: url(#arrowHorizontalRev); }
  .arrow-v { fill: url(#arrowVertical); }
  .arrow-v-rev { fill: url(#arrowVerticalRev); }
</style>
</head>
<body>
<svg class="canvas" viewBox="0 0 1072 1200" xmlns="http://www.w3.org/2000/svg" role="img" aria-label="Analytical cycle: Measure, Inform, Diagnose, Actions around central Data">
  <defs>
    <radialGradient id="topShade" cx="0.38" cy="0.32" r="0.75">
      <stop offset="0" stop-color="var(--disc-light)"/>
      <stop offset="0.6" stop-color="var(--disc-mid)"/>
      <stop offset="1" stop-color="var(--disc-dark)"/>
    </radialGradient>
    <linearGradient id="sideShade" x1="0" y1="0" x2="1" y2="0">
      <stop offset="0" stop-color="var(--side-light)"/>
      <stop offset="0.55" stop-color="var(--side-dark)"/>
      <stop offset="1" stop-color="var(--side-light)"/>
    </linearGradient>
    <linearGradient id="arrowHorizontal" x1="0" y1="0" x2="1" y2="0">
      <stop offset="0" stop-color="var(--arrow-dark)"/>
      <stop offset="0.55" stop-color="var(--arrow-light)"/>
      <stop offset="1" stop-color="var(--arrow-mid)"/>
    </linearGradient>
    <linearGradient id="arrowHorizontalRev" x1="1" y1="0" x2="0" y2="0">
      <stop offset="0" stop-color="var(--arrow-dark)"/>
      <stop offset="0.55" stop-color="var(--arrow-light)"/>
      <stop offset="1" stop-color="var(--arrow-mid)"/>
    </linearGradient>
    <linearGradient id="arrowVertical" x1="0" y1="0" x2="0" y2="1">
      <stop offset="0" stop-color="var(--arrow-dark)"/>
      <stop offset="0.55" stop-color="var(--arrow-light)"/>
      <stop offset="1" stop-color="var(--arrow-mid)"/>
    </linearGradient>
    <linearGradient id="arrowVerticalRev" x1="0" y1="1" x2="0" y2="0">
      <stop offset="0" stop-color="var(--arrow-light)"/>
      <stop offset="0.5" stop-color="var(--arrow-mid)"/>
      <stop offset="1" stop-color="var(--arrow-light)"/>
    </linearGradient>
    <filter id="soften" x="-20%" y="-20%" width="140%" height="140%">
      <feGaussianBlur stdDeviation="8"/>
    </filter>
    <g id="node">
      <circle class="node-shadow" cx="10" cy="38" r="140"/>
      <circle class="node-side" cx="0" cy="26" r="140"/>
      <circle class="node-top" cx="0" cy="0" r="140"/>
    </g>
  </defs>

  <rect class="frame" x="6" y="6" width="1060" height="1188"/>
  <text class="title" x="536" y="150">ANALYTICAL CYCLE</text>

  <!-- cycle arrows -->
  <path class="arrow-h" d="M362 282 Q510 238 648 262 L648 238 L714 296 L648 344 L648 306 Q510 286 362 324 Z"/>
  <path class="arrow-v" d="M836 505 Q878 640 868 742 L900 742 L842 812 L802 736 L834 740 Q846 640 800 512 Z"/>
  <path class="arrow-h-rev" d="M688 978 Q560 950 468 982 L468 958 L398 1020 L470 1068 L470 1032 Q560 1004 688 1022 Z"/>
  <path class="arrow-v-rev" d="M162 872 Q148 700 160 604 L136 604 L178 536 L220 604 L200 604 Q190 700 208 872 Z"/>

  <!-- cycle stages -->
  <g class="stage stage-measure" transform="translate(234 360)">
    <use href="#node"/>
    <text class="node-label" x="0" y="18">Measure</text>
  </g>
  <g class="stage stage-inform" transform="translate(800 360)">
    <use href="#node"/>
    <text class="node-label" x="0" y="18">Inform</text>
  </g>
  <g class="stage stage-data" transform="translate(522 650)">
    <use href="#node"/>
    <text class="node-label" x="0" y="18">Data</text>
  </g>
  <g class="stage stage-actions" transform="translate(230 936)">
    <use href="#node"/>
    <text class="node-label" x="0" y="18">Actions</text>
  </g>
  <g class="stage stage-diagnose" transform="translate(806 936)">
    <use href="#node"/>
    <text class="node-label" x="0" y="18">Diagnose</text>
  </g>
</svg>
</body>
</html>
```